Tandem Hearth Works Pty Ltd

We need business cards for a company based in Perth, we install, service and maintain fire equipment.
On the front we want a great design with our logo and a small spot for our full company name, general company email address and office number. On the back we need space for our name, title, mobile number and email address on the back.

Target Market(s)

Facility managers and commercial/industrial building owners/occupiers.

Contact Information for Business Card

Font styles to use
Sans Serif

Requirements
Must have
• Please only submit 5 of your best samples.
Darker tones are preferred.
Nice to have
• We want to use, black, red and grey. Keep it modern and clean.
I've attached the company logo and a sample of a boarder we use on our emergency plans.
Should not have
• No preference. Let the designer choose.

```html
<!DOCTYPE html>
<html lang="en">
<head>
<meta charset="utf-8">
<title>Tandem Hearth Works – Business Cards</title>
<link href="https://fonts.googleapis.com/css2?family=Arimo:wght@400;700&display=swap" rel="stylesheet">
<style>
  :root {
    --backdrop: #1b1b1c;
    --kraft-light: #dfbd93;
    --kraft-mid: #c79c6b;
    --kraft-dark: #a4754a;
    --ink: #0d0b09;
    --rule: #5a4530;
  }
  * { margin: 0; padding: 0; box-sizing: border-box; }
  html, body {
    width: 1093px;
    height: 1200px;
    overflow: hidden;
    background: var(--backdrop);
    font-family: "Arimo", Arial, sans-serif;
    color: var(--ink);
  }
  .canvas { position: relative; width: 1093px; height: 1200px; }
  .card {
    position: absolute;
    left: 264px;
    width: 580px;
    height: 357px;
    background:
      radial-gradient(ellipse at 30% 0%, var(--kraft-light) 0%, var(--kraft-mid) 55%, var(--kraft-dark) 110%);
    text-align: center;
  }
  .card--front { top: 226px; }
  .card--back { top: 620px; }

  .brand {
    position: absolute;
    top: 92px; left: 0; right: 0;
    display: flex; align-items: center; justify-content: center; gap: 10px;
    font-weight: 700; font-size: 34px; letter-spacing: 1px;
  }
  .brand__square { width: 22px; height: 22px; background: var(--ink); }

  .person { position: absolute; top: 214px; left: 0; right: 0; }
  .person__name { font-weight: 700; font-size: 24px; letter-spacing: 0.3px; line-height: 1.1; }
  .person__title { font-size: 18px; margin-top: 2px; }
  .divider {
    position: absolute; top: 277px; left: 210px; width: 160px;
    height: 1px; background: var(--rule);
  }
  .contact-row {
    position: absolute; left: 0; right: 0;
    display: flex; justify-content: center; align-items: center; gap: 14px;
    font-size: 19px;
  }
  .card--front .contact-row { top: 288px; }
  .card--back .contact-row { top: 236px; font-size: 18px; gap: 18px; }
  .contact { display: flex; align-items: center; gap: 7px; }
  .contact svg { fill: var(--ink); flex: none; }

  .company {
    position: absolute; top: 108px; left: 0; right: 0;
    font-weight: 700; font-size: 25px; line-height: 1.16; letter-spacing: 0.3px;
  }
  .office-phone {
    position: absolute; top: 186px; left: 0; right: 0;
    font-weight: 700; font-size: 27px;
  }
</style>
</head>
<body>
<main class="canvas">

  <section class="card card--front">
    <div class="brand"><span class="brand__square"></span>Tandem Hearth</div>
    <div class="person">
      <div class="person__name">MARCUS ELLERY</div>
      <div class="person__title">Managing Director</div>
    </div>
    <div class="divider"></div>
    <div class="contact-row">
      <span class="contact">
        <svg width="14" height="20" viewBox="0 0 14 20" aria-hidden="true"><path d="M2 0h10a2 2 0 0 1 2 2v16a2 2 0 0 1-2 2H2a2 2 0 0 1-2-2V2a2 2 0 0 1 2-2zm0 3v12h10V3zm5 13.2a1.2 1.2 0 1 0 0 2.4 1.2 1.2 0 0 0 0-2.4z"/></svg>
        789.5550.2146
      </span>
      <span class="contact">
        <svg width="20" height="14" viewBox="0 0 20 14" aria-hidden="true"><path d="M0 0h20v14H0zm2 2v.3l8 6 8-6V2zm0 2.8V12h16V4.8l-8 6z"/></svg>
        name@tandemhearth.com
      </span>
    </div>
  </section>

  <section class="card card--back">
    <div class="company">TANDEM HEARTH<br>WORKS PTY LTD</div>
    <div class="office-phone">789.5550.8310</div>
    <div class="contact-row">
      <span class="contact">
        <svg width="18" height="13" viewBox="0 0 20 14" aria-hidden="true"><path d="M0 0h20v14H0zm2 2v.3l8 6 8-6V2zm0 2.8V12h16V4.8l-8 6z"/></svg>
        info@tandemhearth.com
      </span>
      <span class="contact">
        <svg width="16" height="16" viewBox="0 0 16 16" aria-hidden="true"><path d="M8 0a8 8 0 1 0 0 16A8 8 0 0 0 8 0zm-.8 1.6v2.6H5.1c.5-1.3 1.2-2.2 2.1-2.6zm1.6 0c.9.4 1.6 1.3 2.1 2.6H8.8zM4.3 2.4c-.3.5-.6 1.1-.8 1.8H2.3a6.4 6.4 0 0 1 2-1.8zm7.4 0a6.4 6.4 0 0 1 2 1.8h-1.2c-.2-.7-.5-1.3-.8-1.8zM1.7 5.8h1.5a13 13 0 0 0 0 4.4H1.7a6.4 6.4 0 0 1 0-4.4zm3.1 0h2.4v4.4H4.8a11 11 0 0 1 0-4.4zm4 0h2.4a11 11 0 0 1 0 4.4H8.8zm4 0h1.5a6.4 6.4 0 0 1 0 4.4h-1.5a13 13 0 0 0 0-4.4zm-10.5 6h1.2c.2.7.5 1.3.8 1.8a6.4 6.4 0 0 1-2-1.8zm2.8 0h2.1v2.6c-.9-.4-1.6-1.3-2.1-2.6zm3.7 0h2.1c-.5 1.3-1.2 2.2-2.1 2.6zm3.7 0h1.2a6.4 6.4 0 0 1-2 1.8c.3-.5.6-1.1.8-1.8z"/></svg>
        www.tandemhearth.com
      </span>
    </div>
  </section>

</main>
</body>
</html>
```